Redesign of business card for Cedar Ridge Mechanical

We are looking for a new design for our business cards for Cedar Ridge Mechanical. We are a plumbing & HVAC construction company, operating on the West Coast of Canada and USA. Logo attached.
Industry/Entity Type
Construction - Plumbing & HVAC
Contact Information for Business Card
Name, address, phone numbers, email, website address
Look and feel
Each slider illustrates characteristics of the customer's brand and the style your logo design should communicate.

```html
<!DOCTYPE html>
<html lang="en">
<head>
<meta charset="UTF-8">
<title>Cedar Ridge Mechanical – Business Card</title>
<link rel="stylesheet" href="https://fonts.googleapis.com/css2?family=Montserrat:wght@400;500;700&display=swap">
<style>
  :root {
    --backdrop: #e9e6e2;
    --card-dark: #151515;
    --card-dark-mark: #3a3a3a;
    --card-light: #ffffff;
    --ink: #1a1a1a;
    --ink-soft: #333333;
    --rule: #1a1a1a;
  }
  * { box-sizing: border-box; margin: 0; padding: 0; }
  html, body {
    width: 1200px; height: 900px; overflow: hidden;
    background: var(--backdrop);
    font-family: "Montserrat", sans-serif;
    color: var(--ink);
  }
  .canvas { position: relative; width: 1200px; height: 900px; }
  .card {
    position: absolute; left: 320px;
    width: 560px; height: 320px;
    border-radius: 22px;
    overflow: hidden;
    box-shadow: 0 10px 28px rgba(0,0,0,0.18);
  }
  .card--back {
    top: 110px; background: var(--card-dark);
    display: flex; align-items: center; justify-content: center;
  }
  .card--front { top: 470px; background: var(--card-light); }
  .wordmark {
    font-weight: 700; letter-spacing: 0.06em; text-transform: uppercase;
    display: flex; align-items: center; gap: 12px; white-space: nowrap;
  }
  .wordmark__square { display: block; flex: none; }
  .card--back .wordmark { font-size: 26px; color: var(--card-dark-mark); }
  .card--front .wordmark {
    position: absolute; top: 52px; left: 0; right: 0;
    justify-content: center; font-size: 22px; color: var(--ink);
  }
  .identity {
    position: absolute; top: 140px; left: 40px; width: 190px;
    text-align: right; white-space: nowrap;
  }
  .identity__name { font-size: 25px; font-weight: 700; line-height: 1.2; }
  .identity__role { font-size: 14px; font-weight: 400; color: var(--ink-soft); margin-top: 2px; }
  .divider {
    position: absolute; top: 140px; left: 248px;
    width: 1.5px; height: 80px; background: var(--rule);
  }
  .contact {
    position: absolute; top: 142px; left: 266px; right: 40px;
    list-style: none; font-size: 13px; font-weight: 500; white-space: nowrap;
  }
  .contact__item {
    display: flex; align-items: center; gap: 10px; height: 26px;
  }
  .contact__icon { width: 13px; height: 13px; flex: none; }
  .address {
    position: absolute; top: 248px; left: 60px; right: 40px;
    font-size: 14px; font-weight: 500; white-space: nowrap;
  }
</style>
</head>
<body>
<main class="canvas">
  <section class="card card--back" aria-label="Card back">
    <div class="wordmark">
      <svg class="wordmark__square" width="22" height="22" viewBox="0 0 22 22"><rect width="22" height="22" fill="var(--card-dark-mark)"/></svg>
      Cedar Ridge Mechanical
    </div>
  </section>

  <section class="card card--front" aria-label="Card front">
    <div class="wordmark">
      <svg class="wordmark__square" width="20" height="20" viewBox="0 0 20 20"><rect width="20" height="20" fill="var(--ink)"/></svg>
      Cedar Ridge Mechanical
    </div>

    <div class="identity">
      <p class="identity__name">Daniel Hart</p>
      <p class="identity__role">Managing Director</p>
    </div>

    <div class="divider"></div>

    <ul class="contact">
      <li class="contact__item">
        <svg class="contact__icon" viewBox="0 0 24 24"><path fill="var(--ink)" d="M6.6 10.8a15.1 15.1 0 0 0 6.6 6.6l2.2-2.2a1 1 0 0 1 1-.25 11.4 11.4 0 0 0 3.6.57 1 1 0 0 1 1 1V20a1 1 0 0 1-1 1A17 17 0 0 1 3 4a1 1 0 0 1 1-1h3.5a1 1 0 0 1 1 1c0 1.25.2 2.45.57 3.57a1 1 0 0 1-.25 1z"/></svg>
        555.214.7730
      </li>
      <li class="contact__item">
        <svg class="contact__icon" viewBox="0 0 24 24"><path fill="var(--ink)" d="M2 5h20v14H2z"/><path fill="none" stroke="#fff" stroke-width="2" d="M2 6l10 7 10-7"/></svg>
        info@cedarridgemechanical.com
      </li>
      <li class="contact__item">
        <svg class="contact__icon" viewBox="0 0 24 24"><circle cx="12" cy="12" r="10" fill="none" stroke="var(--ink)" stroke-width="2"/><path fill="none" stroke="var(--ink)" stroke-width="1.6" d="M2 12h20M12 2c3 3 3 17 0 20M12 2c-3 3-3 17 0 20"/></svg>
        www.cedarridgemechanical.com
      </li>
    </ul>

    <p class="address">240 Birch Hollow Road Salem, OR 97301</p>
  </section>
</main>
</body>
</html>
```